BrimFalcon Business Cards

We have a defined brand. Please visit our website to get a feel for the product and the color pallets. www.brimfalcon-example.com

We need an updated, world class business card design. (See the attached existing card design). Please utilize BOTH sides of the card as shown and be creative with the layout. I do want the horse head icon to be positioned as it is with the existing card.

The remainder of the layout can be customized and I also want it vertically oriented.

Attached are the logo files and please use the colors as follows:
Green - #A5CE39
Tan - #CDBD99
Black

Feel free to play with the colors.

```html
<!DOCTYPE html>
<html lang="en">
<head>
<meta charset="utf-8">
<title>BrimFalcon Labs Business Cards</title>
<link rel="stylesheet" href="https://fonts.googleapis.com/css2?family=Roboto+Slab:wght@400;700&family=Exo+2:wght@500&display=swap">
<style>
  :root {
    --green: #a5ce39;
    --black: #111111;
    --white: #ffffff;
    --backdrop: #e6e7e3;
  }
  * { box-sizing: border-box; margin: 0; padding: 0; }
  html, body { width: 1200px; height: 900px; overflow: hidden; }
  body {
    background: var(--backdrop);
    display: flex;
    align-items: center;
    justify-content: center;
    gap: 110px;
    font-family: "Roboto Slab", Georgia, serif;
    color: var(--black);
  }
  .card {
    position: relative;
    width: 360px;
    height: 630px;
    background: var(--green);
    overflow: hidden;
    box-shadow: 0 8px 24px rgba(0,0,0,0.18);
  }
  .brand-mark {
    position: absolute;
    border-radius: 50%;
    background: var(--black);
  }
  .wordmark {
    font-family: "Roboto Slab", Georgia, serif;
    font-weight: 700;
    color: var(--black);
    white-space: nowrap;
    letter-spacing: 0.5px;
  }

  /* Front */
  .card--front .brand-mark { width: 220px; height: 220px; left: 60px; top: 80px; }
  .front-band {
    position: absolute;
    left: 0; right: 0;
    top: 398px;
    height: 112px;
    background: var(--white);
    border-top: 3px solid var(--green);
    border-bottom: 3px solid var(--green);
    outline: 4px solid var(--white);
    display: flex;
    flex-direction: column;
    justify-content: center;
    padding-left: 34px;
  }
  .card--front .wordmark { font-size: 38px; line-height: 1; }
  .tagline {
    font-family: "Exo 2", Arial, sans-serif;
    font-weight: 500;
    font-size: 17px;
    letter-spacing: 4px;
    margin-top: 8px;
  }

  /* Back */
  .back-top {
    position: absolute;
    left: 0; right: 0; top: 0;
    height: 200px;
    background: var(--white);
    border-bottom: 3px solid var(--green);
    outline: 4px solid var(--white);
    padding: 36px 0 0 30px;
  }
  .card--back .wordmark { font-size: 30px; }
  .card--back .brand-mark {
    width: 150px; height: 150px;
    left: 150px; top: 128px;
    border: 5px solid var(--white);
  }
  .person { position: absolute; left: 46px; top: 310px; }
  .person-name { font-size: 25px; font-weight: 700; letter-spacing: 0.5px; }
  .person-role { font-size: 17px; margin-top: 2px; }
  .contact-list {
    position: absolute;
    left: 46px; top: 400px;
    list-style: none;
  }
  .contact-item {
    display: flex;
    align-items: flex-start;
    gap: 14px;
    font-size: 15px;
    line-height: 1.3;
    margin-bottom: 14px;
  }
  .contact-icon {
    flex: none;
    width: 26px; height: 26px;
    border: 2px solid var(--black);
    border-radius: 7px;
    display: flex; align-items: center; justify-content: center;
  }
  .contact-icon svg { width: 14px; height: 14px; }
</style>
</head>
<body>
  <section class="card card--front" aria-label="Business card front">
    <div class="brand-mark" aria-hidden="true"></div>
    <div class="front-band">
      <div class="wordmark">BrimFalcon Labs</div>
      <div class="tagline">Performance Driven EVs</div>
    </div>
  </section>

  <section class="card card--back" aria-label="Business card back">
    <div class="back-top">
      <div class="wordmark">BrimFalcon Labs</div>
    </div>
    <div class="brand-mark" aria-hidden="true"></div>
    <div class="person">
      <div class="person-name">DANA MARLOW</div>
      <div class="person-role">President &amp; CEO</div>
    </div>
    <ul class="contact-list">
      <li class="contact-item">
        <span class="contact-icon"><svg viewBox="0 0 16 16"><path d="M3 1.5l3 3-1.6 1.8a9 9 0 0 0 5.3 5.3L11.5 10l3 3-1.8 2C7 15 1 9 1 3.3z" fill="#111"/></svg></span>
        <span>306 555 0147</span>
      </li>
      <li class="contact-item">
        <span class="contact-icon"><svg viewBox="0 0 16 16"><rect x="1.5" y="3.5" width="13" height="9" fill="none" stroke="#111" stroke-width="1.6"/><path d="M1.5 3.5L8 9l6.5-5.5" fill="none" stroke="#111" stroke-width="1.6"/></svg></span>
        <span>dana@brimfalcon-example.com</span>
      </li>
      <li class="contact-item">
        <span class="contact-icon"><svg viewBox="0 0 16 16" fill="none" stroke="#111" stroke-width="1.4"><circle cx="8" cy="8" r="6.5"/><ellipse cx="8" cy="8" rx="2.8" ry="6.5"/><path d="M1.5 8h13M2.5 4.8h11M2.5 11.2h11"/></svg></span>
        <span>brimfalconlabs-example.com</span>
      </li>
      <li class="contact-item">
        <span class="contact-icon"><svg viewBox="0 0 16 16"><circle cx="8" cy="6" r="4.5" fill="#111"/><circle cx="8" cy="6" r="1.6" fill="#a5ce39"/><path d="M7 10h2v5H7z" fill="#111"/></svg></span>
        <span>Lakeview, Saskatchewan<br>canada</span>
      </li>
    </ul>
  </section>
</body>
</html>
```